ORV Fashion Design Company Needs a New Web Design, Please Click Me

Designers:

PLEASE NOTE: we only need the web page design, not a fully coded website.

Our brand's name is Orbel Vantra, our signature is print. our style is edgy and chic.

The old website is too messy. here's the address:
www.orvdesign.example.cn

The new website's purpose is to show our brand/design and most importantly, sell products, So it should be a combination of a designer official website and online shopping. I want the whole style to be clean, edgy and pioneer, easy to understand. we need a sophisticated online shopping website.

The reference websites are:
liromapek.example.uk
www.qd-besu.example
talemkorv.example
misolvare.example
pardelunitram.example

Please beat their designs :)

Check out our lasted fashion show to get to know us more.

https://www.videohost.example/watch?v=ZkrpLmWnaYd&spfreload=10

The attachments are our Logo and some 2015 Look Book.
(Please let us know if you want to play with our print in this particular web design, we can send the source file.)
Updates

Designers, we really like the design of helenamardoux.example(we have attached a picture of the website) , Can we get a homepage like that? so the designs you submit will be 3 pages. The first one should be a page that only has Shop/Look. then the shop page, it should be nothing but our product which we will list the categories ourself. And the look page should contain all the info. such as news, about us and designers etc. Thank you all for your hard work, we really enjoyed the designs. Added Monday, November 03, 2014

Target Market(s)

Our target audiences are woman aged from 16-40 who like online shopping

Industry/Entity Type

Online Shopping

Number of Pages Required

3 page

Font styles to use
Serif
Sans Serif
Script

Requirements
Must have
• Designers,
• we really like the design of helenamardoux.example(we have attached a picture of the website) , Can we get a homepage like that? so the designs you submit will be 3 pages. The first one should be a page that only has Shop/Look. then the shop page, it should be nothing but our product which we will list the categories ourself. And the look page should contain all the info. such as news, about us and designers etc. Thank you all for your hard work, we really enjoyed the designs.

```html
<!DOCTYPE html>
<html lang="en">
<head>
<meta charset="utf-8">
<title>Orbel Vantra — Home</title>
<link href="https://fonts.googleapis.com/css2?family=Cinzel:wght@400;500&family=Open+Sans:wght@400;600;700;800&display=swap" rel="stylesheet">
<style>
:root{
  --black:#0b0b0b;
  --red:#b20e0e;
  --white:#ffffff;
  --hero-bg:#e2e0e0;
  --panel-grey:#1e1e1e;
  --footer-bg:#ececec;
  --text:#222222;
  --sans:'Open Sans', Arial, sans-serif;
  --serif:'Cinzel', 'Times New Roman', serif;
}
*{margin:0;padding:0;box-sizing:border-box}
html,body{width:840px;height:1200px;overflow:hidden;background:var(--white)}
body{position:relative;font-family:var(--sans);color:var(--text)}

/* navigation */
.brand-box{position:absolute;left:0;top:0;width:149px;height:117px;background:var(--black);z-index:3}
.brand-name{position:absolute;top:12px;left:0;width:149px;text-align:center;color:var(--white);font-family:var(--serif);font-size:9.5px;line-height:10px;letter-spacing:1px}
.brand-mark{display:block;margin:0 auto 8px;width:38px;height:38px;border-radius:50%;background:var(--red)}
.lang-select{position:absolute;left:0;top:88px;width:149px;height:29px;border-top:1px solid #444;color:var(--white);font-size:7px;padding:10px 0 0 15px}
.lang-select svg{position:absolute;right:12px;top:12px}
.main-nav{position:absolute;left:149px;top:0;width:691px;height:35px;display:flex;background:var(--white);z-index:3}
.nav-item{width:115.2px;height:35px;display:flex;align-items:center;justify-content:center;font-size:7.5px;color:#222;border-right:1px solid #ddd}
.nav-item:last-child{border-right:none}
.nav-item.active{background:var(--black);color:var(--white)}

/* hero */
.hero{position:absolute;left:0;top:0;width:840px;height:572px;background:var(--hero-bg)}
.hero-photo{position:absolute;left:0;top:35px;width:840px;height:537px;
  background:
    radial-gradient(ellipse 95px 60px at 618px 95px,#2a2a2a 0%,#5a5a5a 45%,rgba(90,90,90,0) 100%),
    radial-gradient(ellipse 150px 230px at 630px 330px,#fbfbfb 0%,#f1f0f0 45%,rgba(235,234,234,0) 100%),
    radial-gradient(ellipse 170px 120px at 640px 470px,#f6f6f6 0%,rgba(240,240,240,0) 100%),
    linear-gradient(90deg,#e3e1e1 0%,#e0dede 55%,#ecebeb 80%,#d2d0d0 100%)}
.hero-title{position:absolute;left:68px;top:150px}
.hero-the{font-family:var(--sans);font-weight:800;font-size:50px;line-height:50px;color:var(--black)}
.hero-big{font-family:var(--serif);font-weight:400;font-size:118px;line-height:116px;color:var(--black);margin-left:2px}
.hero-red{font-family:var(--sans);font-weight:800;font-size:76px;line-height:70px;color:var(--red)}
.hero-arrow{position:absolute;top:248px}

/* tiles */
.tile{position:absolute;width:131px;height:110px}
.tile-studio{background:
  radial-gradient(ellipse 30px 40px at 35px 55px,#5c6a80 0%,rgba(92,106,128,0) 100%),
  radial-gradient(ellipse 28px 40px at 85px 60px,#f6f6f6 0%,rgba(246,246,246,0) 100%),
  linear-gradient(180deg,#e9eaec 0%,#d8d4cf 60%,#b7a795 100%)}
.tile-portrait{background:
  radial-gradient(ellipse 18px 24px at 65px 38px,#d9b9a3 0%,#c7a18a 60%,rgba(199,161,138,0) 100%),
  radial-gradient(ellipse 70px 40px at 65px 112px,#3a262c 0%,#4a3038 70%,rgba(74,48,56,0) 100%),
  linear-gradient(180deg,#ececec,#d9d9d9)}
.tile-label{position:absolute;left:20px;bottom:18px;color:var(--white)}
.tile-label .strong{display:block;font-family:var(--sans);font-weight:700;font-size:12.5px;line-height:14px;letter-spacing:.5px}
.tile-label .light{display:block;font-family:var(--serif);font-size:16px;line-height:19px;letter-spacing:1px}
.black{background:var(--black)}
.red{background:var(--red)}
.news-panel{position:absolute;left:262px;top:572px;width:578px;height:111px;background:var(--black);color:var(--white)}
.news-title{position:absolute;left:26px;top:27px;font-size:8px;font-weight:600}
.news-body{position:absolute;left:26px;top:45px;width:460px;font-size:6px;line-height:15px}
.news-controls{position:absolute;right:0;top:0;width:54px;height:111px;display:flex;flex-direction:column;gap:1px;background:#000}
.news-controls div{flex:1;background:var(--panel-grey);display:flex;align-items:center;justify-content:center}

/* videos */
.videos-heading{position:absolute;left:39px;top:752px}
.videos-heading .strong{font-family:var(--sans);font-weight:800;font-size:38px;line-height:38px;color:var(--black)}
.videos-heading .light{font-family:var(--serif);font-size:44px;line-height:44px;color:var(--red)}
.videos-copy{position:absolute;left:43px;top:845px;width:270px;font-size:6.6px;line-height:15px;color:#333}
.video-frame{position:absolute;left:353px;top:683px;width:487px;height:297px;background:#111}
.video-still{position:absolute;left:0;top:0;width:487px;height:277px;
  background:
    radial-gradient(ellipse 140px 110px at 370px 130px,#2b2b33 0%,rgba(43,43,51,.55) 50%,rgba(43,43,51,0) 100%),
    linear-gradient(180deg,#d3d5dc 0%,#d6cdd4 40%,#b4b2ba 58%,#6c7078 70%,#8f8f94 78%,#a09c9c 100%)}
.play-button{position:absolute;left:215px;top:120px;width:56px;height:40px;border-radius:8px;background:rgba(30,30,30,.85)}
.play-button svg{position:absolute;left:20px;top:11px}
.player-bar{position:absolute;left:0;top:277px;width:487px;height:20px;background:#111;color:#ddd;font-size:6.5px;display:flex;align-items:center;padding:0 10px;gap:12px}
.player-bar .time{color:#fff}
.player-bar .host{margin-left:auto;font-size:7px;color:#ddd}

/* shop */
.shop-heading{position:absolute;left:0;top:1018px;width:840px;text-align:center;font-weight:800;font-size:37px;line-height:42px;color:var(--black)}
.shop-heading span{color:var(--red)}
.shop-copy{position:absolute;left:60px;top:1074px;width:720px;text-align:center;font-size:6.7px;line-height:15.5px;color:#333}

/* footer */
.site-footer{position:absolute;left:0;top:1157px;width:840px;height:43px;background:var(--footer-bg);font-size:6.8px;color:#333}
.copyright{position:absolute;left:24px;top:17px}
.social{position:absolute;right:22px;top:14px;display:flex;align-items:center;gap:7px}
.social-item{display:flex;align-items:center;gap:3px;font-size:6.5px;font-weight:600;color:#333}
.social-item i{display:block;width:12px;height:12px;border-radius:50%;background:#333}
</style>
</head>
<body>

<header>
  <div class="brand-box">
    <div class="brand-name"><span class="brand-mark"></span>ORV GROUP<br>ORBEL VANTRA</div>
    <div class="lang-select">ENGLISH
      <svg width="9" height="6" viewBox="0 0 9 6"><path d="M1 1l3.5 3.5L8 1" stroke="#fff" stroke-width="1.2" fill="none"/></svg>
    </div>
  </div>
  <nav class="main-nav">
    <div class="nav-item active">HOME</div>
    <div class="nav-item">ONLINE SHOPPING</div>
    <div class="nav-item">ABOUT US</div>
    <div class="nav-item">DESIGNER</div>
    <div class="nav-item">NEWS</div>
    <div class="nav-item">MEMBER CENTER</div>
  </nav>
</header>

<section class="hero">
  <div class="hero-photo" role="img" aria-label="Black and white photo of a model in a white cropped trench jacket and full skirt, hands on hips"></div>
  <div class="hero-title">
    <div class="hero-the">THE</div>
    <div class="hero-big">ORBEL</div>
    <div class="hero-red">VANTRA</div>
  </div>
  <svg class="hero-arrow" style="left:37px" width="20" height="72" viewBox="0 0 20 72"><path d="M19 1L1 36l18 35" stroke="#b9b7b7" stroke-width="1.2" fill="none"/></svg>
  <svg class="hero-arrow" style="left:793px" width="20" height="72" viewBox="0 0 20 72"><path d="M1 1l18 35L1 71" stroke="#8f8d8d" stroke-width="1.2" fill="none"/></svg>
</section>

<section class="tiles">
  <div class="tile tile-studio" style="left:0;top:462px" role="img" aria-label="Designer and model seated in a bright white studio with clothing rails"></div>
  <div class="tile black" style="left:131px;top:462px"><div class="tile-label"><span class="strong">ONLINE</span><span class="light">SHOPPING</span></div></div>
  <div class="tile red" style="left:262px;top:462px"><div class="tile-label"><span class="strong">LATEST</span><span class="light">NEWS</span></div></div>
  <div class="tile red" style="left:0;top:572px;width:130px;height:111px"><div class="tile-label"><span class="strong">ABOUT</span><span class="light">DESIGNER</span></div></div>
  <div class="tile tile-portrait" style="left:131px;top:572px;height:111px" role="img" aria-label="Portrait of the designer in a dark printed shirt"></div>
  <div class="news-panel">
    <div class="news-title">IT IS A LONG ESTABLISHED FACT THAT A READER WILL BE DISTRACTED BY THE READABLE CONTENT</div>
    <p class="news-body">IT IS A LONG ESTABLISHED FACT THAT A READER WILL BE DISTRACTED BY THE READABLE CONTENT OF A PAGE WHEN LOOKING AT ITS LAYOUT. THE POINT OF USING LOREM IPSUM IS THAT IT HAS A MORE-OR-LESS NORMAL DISTRIBUTION OF LETTERS, AS OPPOSED TO USING 'CONTENT HERE, CONTENT HERE', MAKING IT LOOK LIKE READABLE ENGLISH. MANY DESKTOP PUBLISHING PACKAGES...</p>
    <div class="news-controls">
      <div><svg width="10" height="24" viewBox="0 0 10 24"><path d="M1 1l8 11-8 11" stroke="#555" fill="none"/></svg></div>
      <div><svg width="10" height="24" viewBox="0 0 10 24"><path d="M9 1L1 12l8 11" stroke="#555" fill="none"/></svg></div>
    </div>
  </div>
</section>

<section class="videos">
  <div class="videos-heading"><div class="strong">OUR</div><div class="light">VIDEOS</div></div>
  <p class="videos-copy">IT IS A LONG ESTABLISHED FACT THAT A READER WILL BE DISTRACTED BY THE READABLE CONTENT OF A PAGE WHEN LOOKING AT ITS LAYOUT. THE POINT OF USING LOREM IPSUM IS THAT IT HAS A MORE-OR-LESS NORMAL DISTRIBU-TION OF LETTERS, AS OPPOSED TO USING 'CONTENT HERE, CONTENT HERE', MAKING IT LOOK LIKE READABLE ENGLISH. MANY DESKTOP PUBLISHING PACKAGES...</p>
  <div class="video-frame">
    <div class="video-still" role="img" aria-label="Fashion week video still: city skyline at dusk over the river, with the event title"></div>
    <div class="play-button"><svg width="16" height="18" viewBox="0 0 16 18"><path d="M0 0l16 9L0 18z" fill="#3aa0d8"/></svg></div>
    <div class="player-bar">
      <svg width="8" height="8" viewBox="0 0 8 8"><rect x="1" y="0" width="2" height="8" fill="#ccc"/><rect x="5" y="0" width="2" height="8" fill="#ccc"/></svg>
      <svg width="10" height="8" viewBox="0 0 10 8"><path d="M0 2.5h2L5 0v8L2 5.5H0z" fill="#ccc"/><path d="M7 2l3 4M10 2L7 6" stroke="#ccc"/></svg>
      <span><span class="time">0:00</span> / 18:16</span>
      <span class="host">VideoHost</span>
    </div>
  </div>
</section>

<section class="shop">
  <h2 class="shop-heading">SHOP <span>ONLINE</span></h2>
  <p class="shop-copy">IT IS A LONG ESTABLISHED FACT THAT A READER WILL BE DISTRACTED BY THE READABLE CONTENT OF A PAGE WHEN LOOKING AT ITS LAYOUT. THE POINT OF USING LOREM IPSUM IS THAT IT HAS A MORE-OR-LESS NORMAL DISTRIBUTION OF LETTERS, AS OPPOSED TO USING 'CONTENT HERE, CONTENT HERE', MAKING IT LOOK LIKE READABLE ENGLISH. MANY DESKTOP PUBLISHING PACKAGES IT IS A LONG ESTABLISHED FACT THAT A READER WILL BE DISTRACTED BY THE READABLE CONTENT OF A PAGE WHEN LOOKING AT ITS LAYOUT.</p>
</section>

<footer class="site-footer">
  <div class="copyright">COPYRIGHT @ 2014 ORBEL VANTRA. ALL RIGHTS RESERVED.</div>
  <div class="social">
    <span>FOLLOW US :</span>
    <span class="social-item"><i></i>Facelink</span>
    <span class="social-item"><i></i>Circlr</span>
    <span class="social-item"><i></i>Pinvale</span>
    <span class="social-item"><i></i>VideoHost</span>
    <span class="social-item"><i></i>Chirpa</span>
    <span class="social-item"><svg width="10" height="10" viewBox="0 0 9 9"><circle cx="1.5" cy="7.5" r="1.2" fill="#333"/><path d="M0.5 4a4.5 4.5 0 0 1 4.5 4.5M0.5 1a7.5 7.5 0 0 1 7.5 7.5" stroke="#333" stroke-width="1.2" fill="none"/></svg>RSS</span>
  </div>
</footer>

</body>
</html>
```